My mortgage broker firms requires a DL flyer targeting who need finance to build their home.

The design must be professional in presentation as we a small boutique firm that build relationships with our clients through trust.

Refer to my website marrowfinance.com.au to keep the design in similar taste.

Target Market(s)

People in the market to build their 1st home, investment or upgrade.

Industry/Entity Type

Finance

Colors
ec1f27
ffffff
000000

Requirements
Must have
• Catching to the eye. These flyers will be sitting on the desk at builders display homes with many other brochures.
• Premium feel to the design / branding.
Nice to have
• connect to the emotional feelings of building. Not the transaction. ie building a future for the kids or building their investment portfolio which brings financial freedom etc etc
Should not have
• No money pictures

```html
<!DOCTYPE html>
<html lang="en">
<head>
<meta charset="utf-8">
<title>Marrow Finance – Building a home? DL Flyer</title>
<link rel="stylesheet" href="https://fonts.googleapis.com/css2?family=Fira+Sans:wght@300;400;600&display=swap">
<style>
  :root {
    --brand-red: #ec1f27;
    --white: #ffffff;
    --ink: #000000;
    --body-ink: #222222;
    --backdrop: #7a4f2c;
    --photo-warm: #c8b29c;
    --photo-blue: #8aa6c8;
  }
  * { margin: 0; padding: 0; box-sizing: border-box; }
  html, body {
    width: 1200px; height: 706px; overflow: hidden;
    background: var(--backdrop);
    font-family: "Fira Sans", Arial, sans-serif;
  }
  .flyer {
    position: absolute; left: 40px; top: 89px;
    width: 1120px; height: 528px;
    background: var(--white);
    overflow: hidden;
    box-shadow: 3px 4px 8px rgba(0,0,0,0.35);
  }
  .hero-photo {
    position: absolute; left: 0; top: 0; width: 760px; height: 100%;
    background:
      radial-gradient(ellipse at 28% 45%, var(--photo-blue) 0%, rgba(138,166,200,0) 38%),
      linear-gradient(90deg, var(--photo-warm) 0%, #d9c8b6 45%, #ece3d9 68%, rgba(255,255,255,0) 100%);
  }
  .corner-mark {
    position: absolute; left: 18px; top: 4px;
    width: 110px; height: 110px; border-radius: 50%;
    background: var(--brand-red);
    border: 3px solid var(--white);
  }
  .headline-band { position: absolute; left: 319px; top: 16px; width: 801px; height: 62px; }
  .headline-band svg { position: absolute; inset: 0; }
  .headline {
    position: absolute; left: 52px; top: 0; height: 62px;
    display: flex; align-items: center; gap: 26px;
    color: var(--white); font-weight: 600; white-space: nowrap;
  }
  .headline-main { font-size: 45px; letter-spacing: -0.3px; }
  .headline-sub { font-size: 25px; margin-top: 12px; }
  .content { position: absolute; left: 632px; top: 96px; width: 452px; }
  .about-title { color: var(--brand-red); font-size: 24px; font-weight: 400; margin-top: 6px; }
  .about-text {
    margin-top: 5px; font-size: 15px; font-weight: 300; line-height: 20.5px;
    color: var(--body-ink); text-align: justify;
  }
  .highlight {
    margin-top: 26px; color: var(--brand-red);
    font-size: 16.4px; line-height: 24.5px; text-align: justify;
  }
  .benefits { list-style: none; margin-top: 32px; }
  .benefits li {
    position: relative; padding-left: 27px;
    font-size: 15.3px; font-weight: 300; line-height: 20.5px;
    color: var(--body-ink); text-align: justify; margin-bottom: 6px;
  }
  .benefits li::before {
    content: ""; position: absolute; left: 0; top: 5px;
    width: 13px; height: 13px; border-radius: 50%;
    background: var(--brand-red);
  }
  .brand-lockup {
    position: absolute; left: 254px; top: 433px;
    display: flex; align-items: center; gap: 14px;
  }
  .brand-dot {
    width: 76px; height: 76px; border-radius: 50%;
    background: var(--brand-red); border: 3px solid var(--white);
  }
  .brand-name { font-size: 36px; font-weight: 400; color: var(--ink); white-space: nowrap; }
</style>
</head>
<body>
  <main class="flyer">
    <div class="hero-photo" role="img" aria-label="Photo of a smiling young couple on a sofa looking at a tablet with their mortgage broker"></div>
    <div class="corner-mark" aria-hidden="true"></div>

    <header class="headline-band">
      <svg width="801" height="62" viewBox="0 0 801 62" aria-hidden="true">
        <path d="M0 0 H801 V62 H40 Q18 40 0 0 Z" fill="#ec1f27"/>
      </svg>
      <h1 class="headline">
        <span class="headline-main">Building a home?</span>
        <span class="headline-sub">Get the foundations right</span>
      </h1>
    </header>

    <section class="content">
      <h2 class="about-title">About Us</h2>
      <p class="about-text">We are a team of trusted, professional mortgage brokers ready to help you. At Marrow Finance we believe that loan products should be easy to understand, easy to access and allow you peace of mind.</p>
      <p class="highlight">Sometimes the hardest part about building your home is organising the finance. And if you’ve ever done it before, you’ll know it can be trickier than your average mortgage.</p>
      <ul class="benefits">
        <li>Whether it is your first build, an investment property or even an upgrade - its worth getting in touch.</li>
        <li>I will help you find a great home loan, while talking you through ways to reduce your costs and maximise the value of the build.</li>
        <li>Get your financial foundations right - it could make all the difference to the affordability of your project.</li>
      </ul>
    </section>

    <div class="brand-lockup">
      <span class="brand-dot" aria-hidden="true"></span>
      <span class="brand-name">Marrow Finance</span>
    </div>
  </main>
</body>
</html>
```